Label design

Description
I want you to design a label for a skin care product line. I’ve provide the picture of the jar we are using along with the logo. Please note that the logo is available in different colors as well. (See attached) I would like the label to be very clean and straight to the point. Here is some info that I would like to see on the label:
240G
Net wt 8.0z

The content of the jar can be refer to as:

Body cream
Crème de corps
Body butter
Fade cream
Skin tone cream
Lotion pour le corps
Clarifying Body cream
Lightening Cream

The content is also made an exotic component that: “Extraits de noisette de palmiers” meaning nuts extract.

The brand NAME is: Mirevo
The tag line is: Glow softly, every single day

Industry/Entity Type

Skin Care Product

```html
<!DOCTYPE html>
<html lang="en">
<head>
<meta charset="utf-8">
<title>Mirevo – Crème de corps label</title>
<link rel="stylesheet" href="https://fonts.googleapis.com/css2?family=Quicksand:wght@300;400&family=Dancing+Script:wght@400&display=swap">
<style>
  :root {
    --page-bg: #f3f5f6;
    --label-white: #ffffff;
    --orange-light: #f9a61b;
    --orange-mid: #f5800f;
    --orange-deep: #ee5a14;
    --brand-orange: #f47a20;
    --text-white: #ffffff;
  }
  html, body {
    margin: 0;
    padding: 0;
    width: 1068px;
    height: 1200px;
    overflow: hidden;
    background: var(--page-bg);
  }
  .canvas {
    position: relative;
    width: 1068px;
    height: 1200px;
  }
  .label {
    position: absolute;
    left: 140px;
    top: 200px;
    width: 788px;
    height: 608px;
    background: var(--label-white);
    box-shadow: 0 6px 24px rgba(60, 70, 80, 0.12);
  }
  .label svg {
    display: block;
    width: 100%;
    height: 100%;
  }
  .brand-name {
    font-family: "Quicksand", sans-serif;
    font-weight: 300;
    font-size: 46px;
    fill: var(--brand-orange);
  }
  .tagline {
    font-family: "Dancing Script", cursive;
    font-weight: 400;
    font-size: 19px;
    fill: var(--brand-orange);
  }
  .product-name,
  .net-weight {
    font-family: "Quicksand", sans-serif;
    font-weight: 400;
    fill: var(--text-white);
  }
  .product-name { font-size: 26px; }
  .net-weight { font-size: 25px; font-weight: 300; }
</style>
</head>
<body>
  <main class="canvas">
    <section class="label" aria-label="Mirevo body cream jar label">
      <svg viewBox="0 0 590 455" preserveAspectRatio="none" xmlns="http://www.w3.org/2000/svg">
        <defs>
          <linearGradient id="band-orange" x1="0" y1="0" x2="1" y2="0">
            <stop offset="0" stop-color="var(--orange-light)"/>
            <stop offset="0.6" stop-color="var(--orange-mid)"/>
            <stop offset="1" stop-color="var(--orange-deep)"/>
          </linearGradient>
        </defs>

        <path class="top-band" fill="url(#band-orange)"
              d="M0,0 H590 V12 C520,70 440,130 360,160 C260,192 120,170 0,133 Z"/>

        <circle class="name-medallion" cx="295" cy="185" r="97" fill="var(--label-white)"/>

        <path class="bottom-band" fill="url(#band-orange)"
              d="M0,455 C90,390 190,348 290,345 C400,342 500,390 590,428 V455 H0 Z"/>

        <text class="brand-name" x="295" y="252" text-anchor="middle">Mirevo</text>
        <text class="tagline" x="295" y="287" text-anchor="middle">Glow softly, every single day</text>

        <text class="product-name" x="295" y="394" text-anchor="middle">Crème de corps</text>
        <text class="net-weight" x="295" y="437" text-anchor="middle">Net wt 8.0z</text>
      </svg>
    </section>
  </main>
</body>
</html>
```